Business Card Design for Occupational Medicine Start Up Company

We need to design a professional business card. We are a healthcare company providing occupational medicine services to blue collar industries. We are professional, efficient and high quality service providers.

Target Market(s)

Blue Collar Industry: Shipbuilding, Ports, Trucking Companies; The Executives and Safety Officers for these companies

Industry/Entity Type

Healthcare

Contact Information for Business Card

Logo, Name, Title, Email, Phone

Other font styles liked:
• Please match our Brand Guide

Requirements
Must have
• Our Company Colors and Logo

```html
<!DOCTYPE html>
<html lang="en">
<head>
<meta charset="utf-8">
<title>Harborline Clinics – Business Card</title>
<link rel="stylesheet" href="https://fonts.googleapis.com/css2?family=Montserrat:wght@400;500;700;800&display=swap">
<style>
  :root {
    --backdrop: #2a2a2c;
    --navy: #232a86;
    --navy-deep: #1b2170;
    --pattern-light: #3a4fa8;
    --sky: #1e8fd6;
    --amber: #f2a023;
    --paper: #ffffff;
    --ink-grey: #4d4d52;
  }
  * { box-sizing: border-box; margin: 0; padding: 0; }
  html, body {
    width: 1200px; height: 900px; overflow: hidden;
    background: var(--backdrop);
    font-family: "Montserrat", sans-serif;
  }
  .stage {
    position: relative; width: 1200px; height: 900px;
  }
  .card {
    position: absolute; left: 320px;
    width: 560px; height: 320px;
    box-shadow: 0 18px 40px rgba(0,0,0,0.5);
    overflow: hidden;
  }
  /* Back side */
  .card--back { top: 70px; background: var(--navy); }
  .back-pattern {
    position: absolute; inset: 0;
    background: linear-gradient(120deg, var(--navy-deep) 0%, var(--navy) 50%, var(--pattern-light) 100%);
    opacity: 0.9;
  }
  .back-brand {
    position: absolute; right: 70px; top: 142px;
    display: flex; align-items: center; gap: 12px;
    color: var(--paper); font-weight: 700; font-size: 20px; letter-spacing: 0.5px;
  }
  .brand-dot {
    width: 26px; height: 26px; border-radius: 50%; background: currentColor;
  }
  /* Front side */
  .card--front { top: 470px; background: var(--paper); }
  .front-brand {
    position: absolute; right: 40px; top: 56px;
    display: flex; align-items: center; gap: 12px;
    color: var(--navy); font-weight: 700; font-size: 22px; letter-spacing: 0.5px;
  }
  .holder {
    position: absolute; left: 40px; top: 150px;
  }
  .holder-name {
    color: var(--navy); font-weight: 800; font-size: 20px; letter-spacing: 0.3px;
  }
  .holder-title {
    margin-top: 4px; color: var(--ink-grey); font-weight: 500; font-size: 14px;
  }
  .divider {
    position: absolute; left: 40px; right: 40px; top: 210px;
    height: 1.5px; background: var(--amber);
  }
  .contact-list {
    position: absolute; left: 40px; top: 230px;
    list-style: none; color: var(--ink-grey); font-size: 13.5px; font-weight: 500;
  }
  .contact-list li { display: flex; align-items: center; gap: 8px; height: 24px; }
  .contact-list svg { width: 12px; height: 12px; fill: var(--sky); }
  .website {
    position: absolute; right: 40px; top: 232px;
    color: var(--ink-grey); font-size: 13.5px; font-weight: 500;
  }
  .website strong { color: var(--sky); font-weight: 500; }
  .corner-bar {
    position: absolute; right: 40px; bottom: 0;
    width: 170px; height: 12px; background: var(--navy);
  }
</style>
</head>
<body>
<main class="stage">
  <section class="card card--back">
    <div class="back-pattern" role="img" aria-label="Repeating brand pattern in tonal navy and blue"></div>
    <div class="back-brand"><span class="brand-dot"></span>HARBORLINE CLINICS</div>
  </section>

  <section class="card card--front">
    <div class="front-brand"><span class="brand-dot"></span>HARBORLINE CLINICS</div>
    <div class="holder">
      <p class="holder-name">MARK DELANEY</p>
      <p class="holder-title">President</p>
    </div>
    <div class="divider"></div>
    <ul class="contact-list">
      <li>
        <svg viewBox="0 0 24 24" aria-hidden="true"><path d="M6.6 10.8a15.1 15.1 0 0 0 6.6 6.6l2.2-2.2a1 1 0 0 1 1-.25 11.4 11.4 0 0 0 3.6.57 1 1 0 0 1 1 1V20a1 1 0 0 1-1 1A17 17 0 0 1 3 4a1 1 0 0 1 1-1h3.5a1 1 0 0 1 1 1c0 1.25.2 2.45.57 3.6a1 1 0 0 1-.25 1z"/></svg>
        555-318-0472
      </li>
      <li>
        <svg viewBox="0 0 24 24" aria-hidden="true"><path d="M2 5h20v14H2z M2 5l10 8 10-8" fill="none" stroke="#1e8fd6" stroke-width="0"/><path d="M2 6.5V19h20V6.5l-10 7.5z M2.5 5l9.5 7 9.5-7z"/></svg>
        mark@harborlineclinics.com
      </li>
    </ul>
    <p class="website">www.<strong>harborlineclinics</strong>.com</p>
    <div class="corner-bar"></div>
  </section>
</main>
</body>
</html>
```